Elegant Lumocrest Rentals DL flyer

We run a Lumocrest Rentals business - this will be used as a business card as well.

our website is lumocrestrentals.com.au

Front page it sour logo which is attached website details - on the front it needs to say wedding and event hire needs etc..

on the back we will have a spot for 4 products but we want to say there is more so check our the website

A background in the flyer only for example like this would be good http://tapestrova.com/dark-backdrop-image_4726.html

Wedding

Must have
• nice background elegant in style pink and black is the colours

```html
<!DOCTYPE html>
<html lang="en">
<head>
<meta charset="utf-8">
<title>Lumocrest Rentals – Flyer</title>
<link href="https://fonts.googleapis.com/css2?family=Quicksand:wght@400;500;700&family=Roboto:wght@700&display=swap" rel="stylesheet">
<style>
  :root {
    --pink: #e0208a;
    --pink-deep: #b0146a;
    --black: #0d0d0d;
    --ink: #5a5a5a;
    --paper: #ffffff;
    --mist: #e9e9e9;
    --white: #ffffff;
  }
  * { margin: 0; padding: 0; box-sizing: border-box; }
  html, body { width: 1200px; height: 565px; overflow: hidden; background: var(--paper); }
  .flyer {
    position: relative;
    width: 1200px;
    height: 565px;
    overflow: hidden;
    font-family: "Quicksand", sans-serif;
  }
  .backdrop-pattern {
    position: absolute; inset: 0;
    background: radial-gradient(ellipse at 50% 45%, var(--paper) 0%, var(--mist) 100%);
  }
  .bands { position: absolute; inset: 0; width: 1200px; height: 565px; }
  .bottom-pattern {
    position: absolute; left: 0; right: 0; bottom: 0; height: 140px;
    background: linear-gradient(180deg, rgba(40,40,40,0.35), rgba(0,0,0,0));
  }
  .tagline {
    position: absolute;
    color: var(--white);
    font-style: italic;
    font-weight: 500;
    font-size: 21px;
    line-height: 30px;
  }
  .tagline--weddings { right: 852px; top: 84px; text-align: right; }
  .tagline--party { left: 883px; top: 116px; text-align: left; }
  .brand-card {
    position: absolute;
    left: 377px; top: 0;
    width: 476px; height: 336px;
    background: var(--paper);
    box-shadow: 0 3px 10px rgba(0,0,0,0.35);
    display: flex; flex-direction: column; align-items: center; justify-content: center;
    gap: 22px;
  }
  .brand-mark {
    width: 64px; height: 64px; border-radius: 50%;
    background: var(--pink);
  }
  .brand-name {
    font-family: "Quicksand", sans-serif;
    font-weight: 500;
    font-size: 46px;
    color: var(--ink);
    letter-spacing: 1px;
  }
  .phone-badge {
    position: absolute;
    left: 433px; top: 369px;
    width: 363px; height: 67px;
    background: linear-gradient(180deg, var(--pink) 0%, var(--pink-deep) 100%);
    border-radius: 6px;
    box-shadow: 0 2px 6px rgba(0,0,0,0.4);
    color: var(--white);
    font-family: "Roboto", sans-serif;
    font-weight: 700;
    font-size: 48px;
    line-height: 67px;
    text-align: center;
    letter-spacing: 1px;
  }
  .contact { position: absolute; left: 0; right: 0; text-align: center; color: var(--pink); }
  .contact--web { top: 455px; font-size: 30px; font-weight: 700; }
  .contact--email { top: 492px; font-size: 22px; font-weight: 500; }
</style>
</head>
<body>
<main class="flyer">
  <div class="backdrop-pattern" role="img" aria-label="Soft grey floral flourish pattern on white"></div>

  <svg class="bands" viewBox="0 0 1200 565" aria-hidden="true">
    <defs>
      <linearGradient id="bandFade" x1="0" y1="0" x2="0" y2="1">
        <stop offset="0" stop-color="#e0208a"/>
        <stop offset="0.45" stop-color="#8a1052"/>
        <stop offset="1" stop-color="#0d0d0d"/>
      </linearGradient>
      <linearGradient id="baseFade" x1="0" y1="0" x2="0" y2="1">
        <stop offset="0" stop-color="#2a2a2a"/>
        <stop offset="1" stop-color="#050505"/>
      </linearGradient>
    </defs>
    <path d="M0 80 Q190 55 377 50 L377 300 Q190 305 0 335 Z" fill="url(#bandFade)"/>
    <path d="M853 95 Q1030 80 1200 52 L1200 280 Q1030 295 853 300 Z" fill="url(#bandFade)"/>
    <path d="M0 380 Q600 450 1200 385 L1200 565 L0 565 Z" fill="#e0208a"/>
    <path d="M0 392 Q600 462 1200 397 L1200 565 L0 565 Z" fill="url(#baseFade)"/>
  </svg>

  <div class="bottom-pattern" role="img" aria-label="Faint dark floral flourish pattern on black"></div>

  <p class="tagline tagline--weddings">A range of<br>Wedding packages<br>and equipment<br>to make your day special<br>without the extra cost.</p>
  <p class="tagline tagline--party">A range of party<br>products from cocktail<br>tables, cocktail stools,<br>glow products and more<br>to set your party alight.</p>

  <section class="brand-card">
    <span class="brand-mark"></span>
    <span class="brand-name">Lumocrest Rentals</span>
  </section>

  <div class="phone-badge">0491570156</div>
  <p class="contact contact--web">lumocrestrentals.com.au</p>
  <p class="contact contact--email">info@lumocrestrentals.com.au</p>
</main>
</body>
</html>
```